Business Card front and back

I am looking for business card design. I really really like the design file I uploaded named 627788_19250069_3478263_85f427ee_image

Target Market(s)

Corporate Fitness High end Private country club

Industry/Entity Type

Fitness Industry

Contact Information for Business Card

The last image I like as an example I uploaded a bunch of my logos. The file labeled "the signature" is my business card information for you to use

Colors
0054AA
0677BA
7BADD7
CADEEF
E8F1F8

Requirements
Must have
• E-mail sigThe file I uploaded labeled "627788_19250069_3478263_85f427ee_image" with all the plus signs on the back if those could be the logo symbol I uploaded labeled "1 back.png"

```html
<!DOCTYPE html>
<html lang="en">
<head>
<meta charset="utf-8">
<title>Peakform Studio — Business Card</title>
<link rel="stylesheet" href="https://fonts.googleapis.com/css2?family=Play:wght@400;700&display=swap">
<style>
  :root {
    --bg: #1b1b1b;
    --card: #ffffff;
    --ink: #262626;
    --brand: #4a80c4;
    --brand-light: #7bb0ea;
    --brand-dark: #2a4f80;
    --photo-tone: #2a2b2a;
  }
  * { margin: 0; padding: 0; box-sizing: border-box; }
  html, body {
    width: 1093px; height: 1200px; overflow: hidden;
    background: var(--bg);
    font-family: "Play", sans-serif;
    color: var(--ink);
  }
  .card {
    position: absolute;
    left: 265px;
    width: 580px;
    height: 356px;
    border-radius: 24px;
    overflow: hidden;
  }
  .card--front { top: 226px; background: var(--card); }
  .card--back {
    top: 621px;
    background:
      radial-gradient(ellipse at 95% 10%, rgba(123,176,234,0.85) 0%, rgba(123,176,234,0) 55%),
      radial-gradient(ellipse at 0% 100%, rgba(42,79,128,0.9) 0%, rgba(42,79,128,0) 55%),
      var(--brand);
  }

  .brand {
    position: absolute; left: 34px; top: 130px;
    display: flex; align-items: center; gap: 10px;
  }
  .brand__mark { width: 22px; height: 22px; background: var(--brand); }
  .brand__name {
    font-weight: 700; font-size: 25px; letter-spacing: 0.5px;
    color: var(--ink); text-transform: uppercase;
  }

  .contact { position: absolute; left: 34px; top: 234px; list-style: none; }
  .contact__item {
    display: flex; align-items: center; gap: 8px;
    font-size: 16.5px; line-height: 21px; height: 21px;
  }
  .contact__item--location { margin-top: 13px; }
  .contact__icon { width: 15px; height: 15px; flex: none; fill: var(--brand); }

  .portrait {
    position: absolute; left: 362px; top: 67px;
    width: 170px; height: 168px;
    border: 2px solid var(--brand);
    background: radial-gradient(circle at 50% 45%, #5a4f46 0%, #3a3936 35%, var(--photo-tone) 70%);
  }

  .person { position: absolute; right: 45px; top: 274px; text-align: right; }
  .person__name { font-weight: 700; font-size: 25px; line-height: 25px; color: var(--ink); }
  .person__name span { color: var(--brand); }
  .person__role { font-size: 16.5px; line-height: 19px; }

  .back__pattern { position: absolute; inset: 0; }
  .back__name {
    position: absolute; left: 376px; top: 212px;
    transform: translate(-50%, -50%);
    white-space: nowrap;
    color: #ffffff;
    font-weight: 700; font-size: 24px; text-transform: uppercase; letter-spacing: 0.5px;
  }
</style>
</head>
<body>

<section class="card card--front">
  <div class="brand">
    <span class="brand__mark"></span>
    <span class="brand__name">Peakform Studio</span>
  </div>

  <ul class="contact">
    <li class="contact__item">
      <svg class="contact__icon" viewBox="0 0 24 24"><path d="M6.6 10.8a15.1 15.1 0 0 0 6.6 6.6l2.2-2.2c.3-.3.7-.4 1-.2 1.1.4 2.3.6 3.6.6.6 0 1 .4 1 1V20c0 .6-.4 1-1 1A17 17 0 0 1 3 4c0-.6.4-1 1-1h3.5c.6 0 1 .4 1 1 0 1.3.2 2.5.6 3.6.1.3 0 .7-.2 1z"/></svg>
      555-014-2870
    </li>
    <li class="contact__item">
      <svg class="contact__icon" viewBox="0 0 24 24"><path d="M2 5h20v14H2z M2 5l10 8 10-8" stroke="#fff" stroke-width="1.5"/></svg>
      dane@peakformstudio.co
    </li>
    <li class="contact__item">
      <svg class="contact__icon" viewBox="0 0 24 24"><circle cx="12" cy="12" r="10"/><path d="M2 12h20M12 2c3 3 3 17 0 20M12 2c-3 3-3 17 0 20M4 7h16M4 17h16" stroke="#fff" stroke-width="1.2" fill="none"/></svg>
      www.peakformstudio.co
    </li>
    <li class="contact__item contact__item--location">
      <svg class="contact__icon" viewBox="0 0 24 24"><path d="M12 1a8 8 0 0 0-8 8c0 6 8 14 8 14s8-8 8-14a8 8 0 0 0-8-8zm0 11a3 3 0 1 1 0-6 3 3 0 0 1 0 6z"/></svg>
      NW.CT.EA.LK.RV
    </li>
  </ul>

  <div class="portrait" role="img" aria-label="Headshot portrait of the consultant on a dark studio background"></div>

  <div class="person">
    <p class="person__name">DANE <span>MORROW</span></p>
    <p class="person__role">Consultant</p>
  </div>
</section>

<section class="card card--back">
  <div class="back__pattern" role="img" aria-label="Repeating embossed brand pattern in shades of blue, darker at lower left and lighter at upper right"></div>
  <span class="back__name">Peakform Studio</span>
</section>

</body>
</html>
```